Modern Business Card

Modern professional business card with more than just logo and demographic info. Something memorable.

We are a trendy/modern chiropractic group with an emphasis on neurology, hence the minimalist-type brain logo. We want to convey that modern and technical aspect with professionalism and the elite nature of our practice environment.

```html
<!DOCTYPE html>
<html lang="en">
<head>
<meta charset="utf-8">
<title>Meridian Chiropractic – Business Card</title>
<link href="https://fonts.googleapis.com/css2?family=Cormorant+Garamond:wght@600&family=Montserrat:wght@400;500&display=swap" rel="stylesheet">
<style>
  :root {
    --backdrop: #3b3430;
    --card-white: #ffffff;
    --brand-blue: #4a82c8;
    --ink: #1c1c1c;
    --muted: #555555;
    --on-blue: #ffffff;
  }
  * { box-sizing: border-box; margin: 0; padding: 0; }
  html, body {
    width: 1200px; height: 716px; overflow: hidden;
    background: var(--backdrop);
  }
  .stage {
    position: relative; width: 1200px; height: 716px;
    display: flex; align-items: center; justify-content: center; gap: 56px;
  }
  .card {
    position: relative; width: 520px; height: 297px; overflow: hidden;
    box-shadow: 0 14px 30px rgba(0,0,0,.45);
  }

  /* Shared wordmark */
  .wordmark {
    font-family: "Cormorant Garamond", serif; font-weight: 600;
    text-transform: uppercase; line-height: 0.9;
  }
  .wordmark__main { display: block; font-size: 36px; letter-spacing: 0.5px; }
  .wordmark__sub { display: block; font-size: 19px; letter-spacing: 0.5px; }

  /* Front side */
  .card--front { background: var(--card-white); }
  .card--front .wordmark {
    position: absolute; left: 36px; top: 30px; color: var(--ink);
  }
  .person { position: absolute; left: 36px; top: 110px; }
  .person__name {
    font-family: "Cormorant Garamond", serif; font-weight: 600;
    font-size: 20px; letter-spacing: 0.3px; color: var(--brand-blue); text-transform: uppercase;
  }
  .person__title {
    font-family: "Montserrat", sans-serif; font-size: 11px; color: var(--muted); margin-top: 2px;
  }
  .contact-band {
    position: absolute; left: 0; right: 0; bottom: 0; height: 134px;
    background: var(--brand-blue);
  }
  .contact-list {
    position: absolute; left: 30px; top: 20px; list-style: none;
    font-family: "Montserrat", sans-serif; font-size: 11.5px; color: var(--on-blue);
  }
  .contact-list li { display: flex; align-items: center; gap: 8px; margin-bottom: 7px; }
  .contact-list svg { width: 11px; height: 11px; fill: none; stroke: var(--on-blue); stroke-width: 1.6; }
  .address {
    position: absolute; left: 215px; top: 62px; font-style: normal;
    font-family: "Montserrat", sans-serif; font-size: 11.5px; line-height: 1.5; color: var(--on-blue);
  }
  .motif-area {
    position: absolute; background: var(--brand-blue);
  }
  .card--front .motif-area {
    right: 0; top: 26px; bottom: 0; width: 150px;
    border-top-left-radius: 24px;
  }

  /* Back side */
  .card--back { background: var(--brand-blue); }
  .card--back .motif-area {
    left: 0; top: 0; bottom: 0; width: 118px; background: var(--card-white);
    border-top-right-radius: 24px; border-bottom-right-radius: 24px;
  }
  .back-brand {
    position: absolute; left: 172px; top: 112px;
    display: flex; align-items: center; gap: 14px; color: var(--on-blue);
  }
  .back-brand__dot { width: 34px; height: 34px; border-radius: 50%; background: var(--on-blue); }
  .back-brand .wordmark__main { font-size: 44px; }
  .back-brand .wordmark__sub { font-size: 22px; }
</style>
</head>
<body>
<main class="stage">
  <section class="card card--front">
    <div class="motif-area" role="img" aria-label="Brand stripe motif: staggered rounded vertical bars in brand blue"></div>
    <h1 class="wordmark">
      <span class="wordmark__main">Meridian</span>
      <span class="wordmark__sub">Chiropractic</span>
    </h1>
    <div class="person">
      <p class="person__name">Daniel Marsh</p>
      <p class="person__title">Director</p>
    </div>
    <div class="contact-band">
      <ul class="contact-list">
        <li>
          <svg viewBox="0 0 12 12"><path d="M3 1.5 L4.5 4 L3.5 5 Q5 7.5 7 8.5 L8 7.5 L10.5 9 L9.5 10.5 Q4 10 1.5 2.5 Z"/></svg>
          (555) 218-4730
        </li>
        <li>
          <svg viewBox="0 0 12 12"><rect x="1" y="2.5" width="10" height="7"/><path d="M1 2.5 L6 6.5 L11 2.5"/></svg>
          info@meridianchiro.com
        </li>
        <li>
          <svg viewBox="0 0 12 12"><circle cx="6" cy="6" r="5"/><path d="M1 6 H11 M6 1 Q3 6 6 11 Q9 6 6 1"/></svg>
          www.meridianchiro.com
        </li>
      </ul>
      <address class="address">418 Cedar Ridge Lane<br>Salem, OR 97302</address>
    </div>
  </section>

  <section class="card card--back">
    <div class="motif-area" role="img" aria-label="Brand stripe motif: staggered rounded vertical bars in white"></div>
    <div class="back-brand">
      <span class="back-brand__dot"></span>
      <p class="wordmark">
        <span class="wordmark__main">Meridian</span>
        <span class="wordmark__sub">Chiropractic</span>
      </p>
    </div>
  </section>
</main>
</body>
</html>
```